Computer consultant business card

Bexil Software is a newly started computer consulting company. It's a small one-man company that provides mostly Vornix applications but also websites in collaboration with designers. I'm running this company on the side of full time university studies.

I want the final design to be clean and memorable. Be creative! :)

Some inspiration:
http://www.pixelmarta.com/design/48317
http://www.pixelmarta.com/design/2739164/business-card-design-by-frostlynk
http://www.pixelmarta.com/design/604281/business-card-design-by-koralind-vestrabanu

See attachment for my company logo.
Updates

I would like to thank everyone for submitting! I'll need a couple of days to review and ultimately select a design.

Target Market(s)

Non-technical entrepreneurs and small companies.

Industry/Entity Type

University

Requirements
Must have
• My company logo.
In any way, both colors from my logo.
First- and last name, e-mail and phone number.
Double-sided design.
Nice to have
• Something creative with the symbol in my logo

```html
<!DOCTYPE html>
<html lang="en">
<head>
<meta charset="utf-8">
<title>Bexil Software – Business Card</title>
<link href="https://fonts.googleapis.com/css2?family=Arimo:wght@400;700&display=swap" rel="stylesheet">
<style>
  :root {
    --brand-blue: #2a80ff;
    --brand-blue-deep: #1f6fe8;
    --brand-dark: #343132;
    --paper: #ffffff;
    --ink: #1c1c1c;
    --faint-grey: #ececec;
    --faint-blue: #e9f0fd;
    --backdrop: #e6e4e2;
    --divider: #c9c9c9;
  }
  * { box-sizing: border-box; margin: 0; padding: 0; }
  html, body {
    width: 1200px;
    height: 1022px;
    overflow: hidden;
    background: var(--backdrop);
    font-family: "Arimo", Arial, sans-serif;
  }
  .canvas {
    position: relative;
    width: 1200px;
    height: 1022px;
  }
  .card {
    position: absolute;
    width: 498px;
    height: 872px;
    box-shadow: 0 4px 14px rgba(0,0,0,0.25);
  }

  /* Front side */
  .card--front {
    left: 75px;
    top: 70px;
    background: var(--paper);
  }
  .wordmark {
    position: absolute;
    top: 62px;
    left: 0;
    width: 100%;
    display: flex;
    justify-content: center;
    align-items: center;
    gap: 22px;
  }
  .wordmark__dot {
    width: 70px;
    height: 70px;
    border-radius: 50%;
    background: var(--brand-blue);
  }
  .wordmark__name {
    font-size: 84px;
    font-weight: 700;
    color: var(--brand-dark);
    letter-spacing: 1px;
    line-height: 1;
  }
  .front-emblem {
    position: absolute;
    left: 92px;
    top: 262px;
    width: 314px;
    height: 314px;
    border-radius: 50%;
    background: var(--faint-blue);
  }
  .name-band {
    position: absolute;
    left: 0;
    top: 640px;
    width: 100%;
    height: 82px;
    border-top: 3px solid var(--brand-blue);
    border-bottom: 3px solid var(--brand-blue);
    padding: 4px 0;
    background: var(--paper);
  }
  .name-band__fill {
    height: 100%;
    background: var(--brand-blue);
    display: flex;
    align-items: center;
    justify-content: center;
    color: var(--paper);
  }
  .name-band__first {
    font-size: 32px;
    font-weight: 700;
  }
  .name-band__last {
    font-size: 26px;
    font-weight: 400;
    margin-left: 8px;
  }
  .contact {
    position: absolute;
    left: 0;
    top: 772px;
    width: 100%;
    display: flex;
    font-size: 22px;
    color: var(--ink);
    line-height: 30px;
  }
  .contact__address {
    width: 236px;
    text-align: right;
    padding-right: 16px;
  }
  .contact__divider {
    width: 2px;
    height: 62px;
    background: var(--divider);
  }
  .contact__lines {
    padding-left: 16px;
  }
  .contact__line {
    display: flex;
    align-items: center;
    gap: 8px;
  }
  .contact__icon {
    width: 16px;
    height: 16px;
    flex: none;
  }

  /* Back side */
  .card--back {
    left: 627px;
    top: 83px;
    border: 2px solid var(--brand-blue-deep);
    background: radial-gradient(circle at 50% 31%, #ffffff 0%, #cfe2ff 14%, #72aaff 34%, var(--brand-blue) 55%, var(--brand-blue) 100%);
    display: flex;
    align-items: center;
    justify-content: center;
  }
  .back-mark {
    display: flex;
    align-items: center;
    gap: 24px;
    margin-top: -44px;
  }
  .back-mark__dot {
    width: 96px;
    height: 96px;
    border-radius: 50%;
    background: var(--brand-dark);
  }
  .back-mark__name {
    font-size: 104px;
    font-weight: 700;
    color: var(--brand-dark);
    line-height: 1;
  }
</style>
</head>
<body>
<main class="canvas">

  <section class="card card--front" aria-label="Business card front">
    <div class="wordmark">
      <span class="wordmark__dot"></span>
      <span class="wordmark__name">bexil</span>
    </div>

    <div class="front-emblem"></div>

    <div class="name-band">
      <div class="name-band__fill">
        <span class="name-band__first">First Name,</span>
        <span class="name-band__last">Last Name</span>
      </div>
    </div>

    <div class="contact">
      <div class="contact__address">
        <p>00, Complex name</p>
        <p>City, State 0042</p>
      </div>
      <div class="contact__divider"></div>
      <div class="contact__lines">
        <p class="contact__line">
          <svg class="contact__icon" viewBox="0 0 16 16" aria-hidden="true">
            <circle cx="8" cy="8" r="7" fill="none" stroke="#2a80ff" stroke-width="1.5"/>
            <path d="M5.5 4.5 L7 4.5 L7.5 6.5 L6.6 7.2 Q7.5 9 9 9.6 L9.6 8.7 L11.5 9.2 L11.5 10.7 Q8 11.5 5.2 7.5 Q4.8 5.5 5.5 4.5 Z" fill="#2a80ff"/>
          </svg>
          0987 654321
        </p>
        <p class="contact__line">
          <svg class="contact__icon" viewBox="0 0 16 16" aria-hidden="true">
            <rect x="1.5" y="4" width="13" height="9" rx="1.5" fill="#2a80ff"/>
            <path d="M2 4.8 L8 9.2 L14 4.8" fill="none" stroke="#ffffff" stroke-width="1.3"/>
          </svg>
          info@bexil.com
        </p>
      </div>
    </div>
  </section>

  <section class="card card--back" aria-label="Business card back">
    <div class="back-mark">
      <span class="back-mark__dot"></span>
      <span class="back-mark__name">bexil</span>
    </div>
  </section>

</main>
</body>
</html>
```